Website for Vornelix Capital, my new firm that raises money from investors to buy, build, own an...

Vornelix Capital needs a website! We are a new company with very experienced people, who invest in, own and build hotel properties, as well as apartments and other commercial real estate. We seek investors for our projects, and we provide safe, secure returns on their investment in our projects. Our new logo is designed to exhibit strength, class and security, and would like our website to continue on this theme. Our name, Vornelix, is a word-play on a Greek word “aristeia”, which means “excellence” and “a warriors finest moment of glory in war”. If you are in business, you realize that much of it is like war, with strategy and moves and opponents and competitors, and ever-changing economic conditions and threats that make business very much like war. We like to think that we are good at business (war), and so have named our company “Vornelix”, using the founders last name and the word “aristeia” combined. Another definition of "aristeia" is "performing at the peak of one's potential after a long struggle"...again, much like business in real life! The website design should exhibit financial security, smart moves, and positive growth towards a bright future.

Target Market(s)

The target market is smart and wealthy investors, with others such as brokers, cities and government agencies, lenders, sellers, partners, etc also looking at it.

Industry/Entity Type

Investment

Number of Pages Required

5+ page

Font styles to use
Sans Serif

Colors
fec214

Requirements
Must have
• Our website should have a landing page, a "about" or bio page, a projects page and a contact us page. Our new logo uses the colors black and gold, so this should be factored in to our site. The site should be simple, yet impactful and impressive. I have actually two logos, which can be mixed and interchanged in a complimentary way, each with their own unique look.
Nice to have
• I have uploaded a couple screenshots of a website i like, and the simplicity I mention.
Should not have
• The site should not be flashy or complicated or complex or "busy"

```html
<!DOCTYPE html>
<html lang="en">
<head>
<meta charset="utf-8">
<title>Vornelix Capital</title>
<link rel="stylesheet" href="https://fonts.googleapis.com/css2?family=Michroma&family=Raleway:wght@400;500;600;700;800&display=swap">
<style>
:root{
  --gold:#c8962a;
  --gold-light:#d9a83a;
  --ink:#1b1b1b;
  --text:#555;
  --white:#fff;
  --dark:#202224;
  --field:#ffffff;
}
*{box-sizing:border-box;margin:0;padding:0}
html,body{width:1200px;height:3072px;overflow:hidden;background:#fff}
body{position:relative;font-family:"Raleway",sans-serif;color:var(--text)}
.abs{position:absolute}

/* top bar */
.topbar{left:0;top:0;width:1200px;height:41px;background:var(--gold);color:#fff;font-size:14px;font-weight:600;display:flex;justify-content:flex-end;align-items:center;gap:26px;padding-right:78px}
.topbar span{display:flex;align-items:center;gap:8px}

/* header */
.header{left:0;top:41px;width:1200px;height:86px;background:#fff;box-shadow:0 2px 6px rgba(0,0,0,.08);z-index:2}
.brand{left:78px;top:26px;display:flex;align-items:center;gap:12px;font-family:"Michroma",sans-serif;font-size:18px;line-height:26px;color:var(--ink);letter-spacing:1px}
.brand i{width:26px;height:26px;background:var(--gold);display:block}
.nav{right:78px;top:34px;display:flex;gap:30px;font-size:14px;line-height:18px;font-weight:600;color:#333;letter-spacing:.5px}
.nav .active{color:var(--gold)}

/* hero */
.hero{left:0;top:127px;width:1200px;height:549px;background:linear-gradient(180deg,#3a4a5e 0%,#55677b 45%,#4a4e4c 75%,#2f3230 100%)}
.hero-title{left:0;top:300px;width:1200px;text-align:center;color:#fff;font-weight:800;font-size:45px;line-height:56px;text-shadow:0 2px 6px rgba(0,0,0,.4)}
.btn{background:var(--gold);color:#fff;font-family:"Michroma",sans-serif;font-size:17px;line-height:1;letter-spacing:1px;display:flex;align-items:center;justify-content:center}
.hero-btn{left:460px;top:440px;width:280px;height:56px}

/* welcome */
.eyebrow{left:0;width:1200px;text-align:center;color:var(--gold);font-family:"Michroma",sans-serif;font-size:20px;line-height:26px;letter-spacing:2px}
.section-title{left:0;width:1200px;text-align:center;color:var(--ink);font-family:"Michroma",sans-serif;font-weight:400;font-size:40px;line-height:50px;letter-spacing:3px}
.rule{left:578px;width:44px;height:3px;background:var(--gold)}
.intro{left:228px;top:868px;width:744px;text-align:center;font-size:13.5px;line-height:27px;color:#666}
.intro p+p{margin-top:12px}
.learn-btn{left:500px;top:1059px;width:200px;height:49px}

/* about band */
.about{left:0;top:1171px;width:1200px;height:500px;background:linear-gradient(135deg,#3c3f44 0%,#23262a 55%,#15171a 100%)}
.about-frame{left:197px;top:1270px;width:806px;height:307px;border:5px solid rgba(255,255,255,.55)}
.portrait{left:215px;top:1200px;width:338px;height:471px;background:linear-gradient(180deg,#8c97a5 0%,#2e3c5c 45%,#1c2640 100%);border-radius:150px 150px 0 0}
.about-title{left:582px;top:1312px;color:#fff;font-family:"Michroma",sans-serif;font-weight:400;font-size:35px;line-height:44px;letter-spacing:2px}
.about-sub{left:588px;top:1359px;color:var(--gold-light);font-size:15px;line-height:20px;font-weight:700}
.service{width:140px;text-align:center;color:#fff;font-size:14px;line-height:20px}
.service .circle{width:88px;height:88px;border-radius:50%;background:var(--gold);margin:0 auto 12px;display:flex;align-items:center;justify-content:center}

/* projects */
.project{width:338px;height:230px}
.p1{background:linear-gradient(180deg,#6fa3d8 0%,#d9dfe5 55%,#6b6c6e 100%)}
.p2{background:linear-gradient(180deg,#b9a05a,#a78a3e)}
.p3{background:linear-gradient(180deg,#9cc7e8 0%,#3aa3d0 60%,#b6874f 100%)}
.p4{background:linear-gradient(180deg,#5f95d2 0%,#a55b45 55%,#4c5c3a 100%)}
.p5{background:linear-gradient(180deg,#7e9ea8 0%,#3f4a63 50%,#5d8a3d 100%)}
.p6{background:linear-gradient(180deg,#2e4e7c 0%,#455a7a 55%,#2b2a2c 100%)}
.overlay{left:0;top:0;width:100%;height:100%;display:flex;align-items:center;justify-content:center}
.view-btn{left:512px;top:2345px;width:176px;height:49px}

/* contact */
.contact{left:0;top:2462px;width:1200px;height:553px;background:linear-gradient(135deg,#2d2e30,#1c1d1f)}
.contact-title{left:0;top:2520px;width:1200px;text-align:center;color:#fff;font-family:"Michroma",sans-serif;font-weight:400;font-size:38px;line-height:48px;letter-spacing:3px}
.field{left:78px;width:438px;background:var(--field);color:#999;font-size:13px;line-height:18px;padding:16px 18px}
.submit{left:78px;top:2894px;width:164px;height:55px;font-size:18px}
.map{left:526px;top:2609px;width:277px;height:277px;background:linear-gradient(135deg,#e6e3dc,#d8d5cc)}
.address{left:856px;top:2610px;width:290px;color:#ddd;font-size:13px;line-height:21px}
.address h3{font-family:"Michroma",sans-serif;font-weight:400;color:#fff;font-size:15px;line-height:22px;letter-spacing:1px;margin-bottom:16px}
.addr-row{display:flex;gap:14px;margin-bottom:14px}
.addr-row svg{flex:none;margin-top:2px}
.addr-row .name{color:var(--gold-light);font-weight:600}

/* footer */
.footer{left:0;top:3015px;width:1200px;height:57px;background:var(--gold);color:#fff;font-size:13.5px;font-weight:600;display:flex;align-items:center;justify-content:center}
</style>
</head>
<body>

<div class="abs topbar">
  <span><svg width="16" height="16" viewBox="0 0 24 24" fill="#fff"><path d="M6.6 10.8a15 15 0 0 0 6.6 6.6l2.2-2.2a1 1 0 0 1 1-.25 11 11 0 0 0 3.6.6 1 1 0 0 1 1 1V20a1 1 0 0 1-1 1A17 17 0 0 1 3 4a1 1 0 0 1 1-1h3.5a1 1 0 0 1 1 1c0 1.25.2 2.45.6 3.6a1 1 0 0 1-.25 1z"/></svg>123 456 7890</span>
  <span><svg width="18" height="14" viewBox="0 0 24 18" fill="#fff"><path d="M0 0h24v2L12 10 0 2z"/><path d="M0 4.5l12 8 12-8V18H0z"/></svg>info@vornelix.com</span>
</div>

<header class="abs header">
  <div class="abs brand"><i></i>Vornelix Capital</div>
  <nav class="abs nav">
    <span class="active">HOME ▾</span><span>ABOUT US</span><span>PROJECTS</span><span>CONTACT US</span>
  </nav>
</header>

<section class="abs hero" role="img" aria-label="Photo of a modern glass office building with a paved walkway and palm trees"></section>
<h1 class="abs hero-title">Manage Your Investments<br>Easily and Effectivelt</h1>
<div class="abs btn hero-btn">GET FREE QUOTE</div>

<div class="abs eyebrow" style="top:738px">WELCOME TO</div>
<h2 class="abs section-title" style="top:772px">VORNELIX CAPITAL</h2>
<div class="abs rule" style="top:836px"></div>
<div class="abs intro">
  <p>Lorem Ipsum is simply dummy text of the printing and typesetting industry. Lorem Ipsum has been the industry's standard dummy text ever since thes, when an unknown printer</p>
  <p>Lorem Ipsum is simply dummy text of the printing and typesetting industry. Lorem Ipsum has been the industry's standard dummy text ever since the 1500s, when an unknown printer took a galley of type and scrambled it to make a type specimen book. It has survived not only five centuries, but also the leap into electronic typesetting, remaining essentially unchanged.</p>
</div>
<div class="abs btn learn-btn">LEARN MORE</div>

<section class="abs about" role="img" aria-label="Dark photo of glass skyscrapers seen from below"></section>
<div class="abs about-frame"></div>
<div class="abs portrait" role="img" aria-label="Photo of a businessman in a dark suit with arms crossed"></div>
<h2 class="abs about-title">ABOUT US</h2>
<div class="abs about-sub">We Provide Safe, Secure Returns</div>

<div class="abs service" style="left:555px;top:1397px">
  <div class="circle"><svg width="40" height="44" viewBox="0 0 40 44" fill="#fff"><rect x="4" y="8" width="18" height="34"/><rect x="24" y="18" width="12" height="24"/><g fill="#c8962a"><rect x="8" y="12" width="4" height="4"/><rect x="14" y="12" width="4" height="4"/><rect x="8" y="20" width="4" height="4"/><rect x="14" y="20" width="4" height="4"/><rect x="8" y="28" width="4" height="4"/><rect x="14" y="28" width="4" height="4"/><rect x="28" y="24" width="4" height="4"/><rect x="28" y="32" width="4" height="4"/></g></svg></div>
  Build Hotel<br>Properties
</div>
<div class="abs service" style="left:684px;top:1397px">
  <div class="circle"><svg width="36" height="44" viewBox="0 0 36 44" fill="#fff"><rect x="6" y="4" width="24" height="38"/><g fill="#c8962a"><rect x="10" y="9" width="16" height="3"/><rect x="10" y="16" width="16" height="3"/><rect x="10" y="23" width="16" height="3"/><rect x="10" y="30" width="16" height="3"/><rect x="15" y="36" width="6" height="6"/></g></svg></div>
  Apartments
</div>
<div class="abs service" style="left:815px;top:1397px">
  <div class="circle"><svg width="44" height="42" viewBox="0 0 44 42" fill="#fff"><path d="M22 2 40 14H4z"/><rect x="6" y="16" width="32" height="24"/><g fill="#c8962a"><rect x="10" y="20" width="5" height="5"/><rect x="19.5" y="20" width="5" height="5"/><rect x="29" y="20" width="5" height="5"/><rect x="10" y="29" width="5" height="5"/><rect x="29" y="29" width="5" height="5"/><rect x="19" y="29" width="6" height="11"/></g></svg></div>
  Commercial<br>Real Estate
</div>

<div class="abs eyebrow" style="top:1731px">WHAT WE DO</div>
<h2 class="abs section-title" style="top:1764px;font-size:37px">OUR PROJECTS</h2>
<div class="abs rule" style="top:1823px"></div>

<div class="abs project p1" style="left:78px;top:1855px" role="img" aria-label="Photo of a modern office building and parking lot"></div>
<div class="abs project p2" style="left:430px;top:1855px" role="img" aria-label="Photo of suburban houses under a gold hover tint">
  <div class="abs overlay"><svg width="40" height="40" viewBox="0 0 40 40" fill="none" stroke="#fff" stroke-width="3"><circle cx="17" cy="17" r="12"/><path d="M26 26l10 10M17 11v12M11 17h12"/></svg></div>
</div>
<div class="abs project p3" style="left:784px;top:1855px" role="img" aria-label="Photo of a villa terrace with a swimming pool and sea view"></div>
<div class="abs project p4" style="left:78px;top:2099px" role="img" aria-label="Photo of a brick apartment building with balconies"></div>
<div class="abs project p5" style="left:430px;top:2099px" role="img" aria-label="Photo of a blue family house with a front lawn"></div>
<div class="abs project p6" style="left:784px;top:2099px" role="img" aria-label="Photo of a lit retail building at dusk"></div>
<div class="abs btn view-btn">VIEW MORE</div>

<section class="abs contact" role="img" aria-label="Dark background photo of architectural drawings and tools"></section>
<h2 class="abs contact-title">CONTACT US</h2>
<div class="abs field" style="top:2609px;height:51px">Name</div>
<div class="abs field" style="top:2665px;height:53px">E-Mail</div>
<div class="abs field" style="top:2722px;height:53px">Phone</div>
<div class="abs field" style="top:2779px;height:105px">Message</div>
<div class="abs btn submit">SUBMIT</div>
<div class="abs map" role="img" aria-label="Street map showing the office location"></div>

<div class="abs address">
  <h3>CONTACT ADDRESS</h3>
  <div class="addr-row">
    <svg width="18" height="22" viewBox="0 0 18 22" fill="none" stroke="#c8962a" stroke-width="2"><path d="M9 21s7-7 7-12A7 7 0 0 0 2 9c0 5 7 12 7 12z"/><circle cx="9" cy="9" r="2.5"/></svg>
    <div><div class="name">VORNELIX CAPITAL</div>101 - Lorem text<br>Lorem ipsum is simple print<br>dummy text of industry.</div>
  </div>
  <div class="addr-row">
    <svg width="18" height="18" viewBox="0 0 24 24" fill="none" stroke="#c8962a" stroke-width="2"><path d="M6.6 10.8a15 15 0 0 0 6.6 6.6l2.2-2.2 4.6 1V20A17 17 0 0 1 3 4h4.2l1 4.6z"/></svg>
    <div style="font-weight:600">+0 123 456 7890</div>
  </div>
  <div class="addr-row">
    <svg width="18" height="20" viewBox="0 0 16 22" fill="none" stroke="#c8962a" stroke-width="2"><rect x="2" y="1" width="12" height="20" rx="2"/><path d="M6 17h4"/></svg>
    <div>+0 123 456 7890</div>
  </div>
  <div class="addr-row">
    <svg width="18" height="16" viewBox="0 0 24 18" fill="none" stroke="#c8962a" stroke-width="2"><rect x="1" y="1" width="22" height="16"/><path d="M1 1l11 9 11-9"/></svg>
    <div>info@vornelix.com</div>
  </div>
</div>

<footer class="abs footer">©VORNELIX CAPITAL - 2018 All Right Reserved.</footer>

</body>
</html>
```